Design of a promotional offer flyer required to promote low-cost websites to 1-man band businesses

I want a flyer designed - either a double-sided A5 flyer or even A4 folded into a third double-sided. The flyer is to showcase a new service - low-cost websites for 1-man-band businesses, business startups and tradesmen in England. Look at the copy, find some pix and let me know! Flyer will be printed and used as an image on my website too. Pix could be related to some of the target groups. We need to stress the simple message that websites start from £5 per week and this is an-all-in-one fee.

Target Market(s)

Tradesmen, business start ups and 1-man band businesses that want a website

Industry/Entity Type

Small Business

Contact Information for Business Card

All contact details and name of business to be confirmed shortly

Font styles to use
Serif

Requirements
Must have
• Basic messages from copy for flyer i.e. websites from £5 per week and what each client gets for that price to be included on the business card! Please read copy for the flyer.
Nice to have
• Nice background image or series of small images relevant to the target audience. Again, see list of targets from copy for flyer.
Should not have
• I don't want exact or similar design to my main business Blue Harbour Promotions. The new flyer and business card should be a different and distinct branding to that of Blue Harbour Promotions. Aimed at a more economical style, whilst looking professional, but relevant to the target audiences.

```html
<!DOCTYPE html>
<html lang="en">
<head>
<meta charset="utf-8">
<title>Low-cost websites flyer</title>
<link rel="stylesheet" href="https://fonts.googleapis.com/css2?family=Oswald:wght@400;500;600;700&family=Lato:wght@400;700&family=Montserrat:wght@700&display=swap">
<style>
  :root{
    --backdrop:#8d8d8d;
    --paper:#ffffff;
    --red:#e41111;
    --red-deep:#c80d0d;
    --ink:#1a1a1a;
    --slate:#3d3d3d;
    --yellow:#f6f000;
    --gold:#ffe600;
    --black:#0e0e0e;
  }
  *{margin:0;padding:0;box-sizing:border-box}
  html,body{width:1200px;height:848px;overflow:hidden;background:var(--backdrop)}
  body{position:relative;font-family:'Lato',sans-serif;color:var(--ink)}
  .page{position:absolute;width:561px;height:785px;background:var(--paper);overflow:hidden}
  .page--front{left:30px;top:29px}
  .page--back{left:609px;top:26px}

  .photo{position:absolute}
  .photo--hero{left:50px;top:27px;width:472px;height:376px;
    background:radial-gradient(ellipse at 60% 45%,#d9b8a0 0%,#7f8fa8 45%,#e9edf2 80%,#fff 100%)}
  .headline{position:absolute;left:0;width:100%;text-align:center;font-family:'Oswald',sans-serif;font-weight:700;text-transform:uppercase;line-height:1}
  .headline--main{top:412px;font-size:45px;color:var(--red);letter-spacing:.5px}
  .headline--sub{top:458px;font-size:35px;color:var(--slate);font-weight:600}

  .price-band{position:absolute;left:0;top:512px;width:100%;height:109px;background:linear-gradient(90deg,var(--red-deep),var(--red) 50%,var(--red-deep))}
  .price-band__lead{position:absolute;left:40px;top:20px;width:240px;color:#fff;font-family:'Oswald',sans-serif;font-weight:400;font-size:19px;line-height:22px;letter-spacing:-.2px}
  .price-band__lead b{font-weight:700}
  .price-band__rule{position:absolute;left:290px;top:15px;width:2px;height:80px;background:#fff}
  .price-band__price{position:absolute;left:306px;top:10px;color:var(--gold);font-family:'Oswald',sans-serif;font-weight:700;font-size:45px;line-height:1}
  .price-band__note{position:absolute;left:306px;top:66px;color:var(--gold);font-family:'Oswald',sans-serif;font-weight:600;font-size:27px;line-height:1}

  .audience{position:absolute;left:0;top:621px;width:100%;height:86px;background:var(--black);color:#fff;font-size:12.6px;line-height:15.5px;padding:10px 44px 0 45px;text-align:justify;text-align-last:center}
  .stripe{position:absolute;left:0;width:100%}
  .stripe--red{top:707px;height:10px;background:var(--red)}
  .stripe--black{top:743px;height:42px;background:var(--black)}

  .top-bar{position:absolute;left:0;top:0;width:100%;height:28px;background:var(--red)}
  .benefits__title{position:absolute;left:33px;top:44px;font-family:'Oswald',sans-serif;font-weight:700;font-size:35px;color:var(--ink);letter-spacing:.2px}
  .photo--presenter{left:302px;top:36px;width:244px;height:204px;
    background:linear-gradient(160deg,#fff 0%,#c9b3a6 40%,#4a4a50 75%,#fff 100%)}
  .benefits{position:absolute;left:36px;top:100px;width:500px;list-style:none;font-size:12.9px;line-height:15.4px;color:#222}
  .benefits li{position:relative;padding-left:22px;margin-bottom:5.3px}
  .benefits li svg{position:absolute;left:0;top:2px;width:13px;height:12px}
  .benefits .narrow{width:240px}
  .benefits b{font-weight:700}

  .fee__intro{position:absolute;left:0;top:394px;width:342px;text-align:center;font-family:'Lato',sans-serif;font-weight:700;font-size:17px;color:var(--ink)}
  .fee__band{position:absolute;left:0;top:419px;width:342px;height:48px;background:var(--yellow);text-align:center;font-size:15.6px;line-height:20px;padding-top:4px;color:var(--ink)}
  .fee__band .hi{color:var(--red)}
  .photo--devices{left:345px;top:385px;width:198px;height:116px;
    background:linear-gradient(180deg,#3d3f46 0%,#6d717b 55%,#e6e6e6 100%)}

  .promo__title{position:absolute;left:0;top:487px;width:414px;text-align:center;font-family:'Montserrat',sans-serif;font-weight:700;font-size:23px;color:var(--red);letter-spacing:.5px}
  .promo__box{position:absolute;left:27px;top:523px;width:384px;height:104px;border:2px solid var(--ink);background:#fff;text-align:center;font-family:'Oswald',sans-serif}
  .promo__line{font-size:18px;font-weight:600;color:var(--slate);line-height:25px}
  .promo__line:first-child{margin-top:8px}
  .promo__cost{font-size:29px;font-weight:700;color:var(--red);line-height:36px}

  .photo--installer{left:416px;top:540px;width:145px;height:142px;
    background:linear-gradient(170deg,#ffffff 0%,#d8c2a8 35%,#b37a4a 75%,#a66a3c 100%)}
  .contact{position:absolute;left:0;top:682px;width:100%;height:76px;background:var(--red);color:#fff}
  .contact__inner{position:absolute;left:22px;top:0;width:403px;text-align:center}
  .contact__line{font-family:'Oswald',sans-serif;font-weight:600;font-size:24px;line-height:1;padding-top:8px;white-space:nowrap}
  .contact__sep{display:inline-block;width:2px;height:26px;background:#fff;vertical-align:-4px;margin:0 4px}
  .contact__small{font-size:13px;line-height:16px;margin-top:4px}
  .stripe--foot{top:758px;height:27px;background:var(--black)}
</style>
</head>
<body>
<svg width="0" height="0" style="position:absolute" aria-hidden="true">
  <symbol id="tick" viewBox="0 0 13 12"><path d="M1 6.5 L4.5 10 L12 1.5" fill="none" stroke="#e41111" stroke-width="2.4" stroke-linecap="round" stroke-linejoin="round"/></symbol>
</svg>

<section class="page page--front">
  <div class="photo photo--hero" role="img" aria-label="Smiling woman pointing at a laptop showing app icons and a smartphone"></div>
  <h1 class="headline headline--main">Want a website</h1>
  <p class="headline headline--sub">Without it costing the earth?</p>
  <div class="price-band">
    <p class="price-band__lead">Professionally-designed websites for <b>tradesmen</b>, business start-ups and <b>1-man bands</b> from only</p>
    <span class="price-band__rule"></span>
    <p class="price-band__price">£5 per week</p>
    <p class="price-band__note">&amp; NO upfront costs!</p>
  </div>
  <p class="audience">Suitable for plumbers, electricians, roofers, builders, painters and decorators, joiners, business start-ups, 1-man bands such as hairdressers, photographers, fitness instructors, window cleaners, beauticians, gardeners, odd job men, wheelie bin cleaners, IFAs or self-employed consultants.</p>
  <div class="stripe stripe--red"></div>
  <div class="stripe stripe--black"></div>
</section>

<section class="page page--back">
  <div class="top-bar"></div>
  <div class="photo photo--presenter" role="img" aria-label="Woman presenting a laptop displaying a website template"></div>
  <h2 class="benefits__title">Here’s what you get :</h2>
  <ul class="benefits">
    <li class="narrow"><svg><use href="#tick"/></svg>Professionally-designed 1-page or 5-page website (Home, About Us, Services, Contact Us, News)</li>
    <li class="narrow"><svg><use href="#tick"/></svg>Responsive design that displays properly on mobiles and tablets</li>
    <li><svg><use href="#tick"/></svg>On-going changes and updates</li>
    <li><svg><use href="#tick"/></svg>All text written for you</li>
    <li><svg><use href="#tick"/></svg>Photographs (Royalty-free stock images)</li>
    <li><svg><use href="#tick"/></svg>Professional email addresses e.g. info@yourcompany.co.uk, <b>sales@yourcompany.co.uk</b> and <b>yourname@yourcompany.co.uk</b>. We’ll even set up these email addresses on your PC and laptop!</li>
    <li><svg><use href="#tick"/></svg>Links to your social media accounts</li>
    <li><svg><use href="#tick"/></svg>Up to 2 hours’ changes each month to content, pix, and adding new pages</li>
    <li><svg><use href="#tick"/></svg>Professional hosting for your website and email</li>
    <li><svg><use href="#tick"/></svg>No upfront cost! Just weekly, monthly or annual invoice - you choose!</li>
  </ul>

  <p class="fee__intro">For an-all-in fee from</p>
  <p class="fee__band"><span class="hi">only £5 per week for a 1-page website</span><br>or <span class="hi">£10 per week for a 5-page website.</span></p>
  <div class="photo photo--devices" role="img" aria-label="Desktop, laptop, tablet and phone showing a responsive website"></div>

  <p class="promo__title">Promotional Offer :</p>
  <div class="photo photo--installer" role="img" aria-label="Electrician fitting a wall socket"></div>
  <div class="promo__box">
    <p class="promo__line">order your new 5-page website before ............</p>
    <p class="promo__line">and we’ll set up a Chatterbook Page for FREE.</p>
    <p class="promo__cost">Normal Cost: £97 plus VAT!</p>
  </div>

  <div class="contact">
    <div class="contact__inner">
      <p class="contact__line">Email: TBC<span class="contact__sep"></span>Visit www. TBC<span class="contact__sep"></span>Call:&nbsp; TBC</p>
      <p class="contact__small">For further information or to order.<br>Full terms and conditions at www. TBC.&nbsp; All fees plus VAT.</p>
    </div>
  </div>
  <div class="stripe stripe--foot"></div>
</section>
</body>
</html>
```